Bluecrest Learning Corps by graduating students from college in two years

Based on the logo design, create stationary and business cards for
Dr. Venrel T Oskamp, CEO, (703) 482-1736
and Marisa Deltoft, Respresentative, (301) 647-2208
Address: 4719 Pellham Court, Ashbrook Station, VA 22184
Incorporate elelments of the logo

Target Market(s)

USA

Font styles to use
Other font styles liked:
• match with the logo type style

```html
<!DOCTYPE html>
<html lang="en">
<head>
<meta charset="utf-8">
<title>Bluecrest Learning Corps – Letterhead</title>
<link rel="stylesheet" href="https://fonts.googleapis.com/css2?family=Arimo:wght@400;700&family=Montserrat:wght@600;700&display=swap">
<style>
  :root {
    --navy: #0c1f5c;
    --gold: #f7c22e;
    --white: #ffffff;
    --ink: #3a3a3a;
    --rule: #8a8a8a;
    --backdrop: #e6e7e8;
  }
  * { margin: 0; padding: 0; box-sizing: border-box; }
  html, body { width: 1200px; height: 960px; overflow: hidden; background: var(--backdrop); }
  .letterhead {
    position: absolute; left: 260px; top: 40px; width: 680px; height: 880px;
    background: var(--white); box-shadow: 0 4px 18px rgba(0,0,0,.12);
    font-family: "Arimo", Arial, sans-serif; color: var(--ink);
  }
  .header-wave { position: absolute; left: 0; top: 0; width: 680px; height: 200px; }
  .brand {
    position: absolute; left: 30px; top: 70px; display: flex; align-items: center; gap: 10px;
  }
  .brand-dot { width: 26px; height: 26px; border-radius: 50%; background: var(--gold); }
  .brand-name {
    font-family: "Arimo", Arial, sans-serif; font-weight: 700; font-size: 15px;
    color: var(--white); width: 120px; line-height: 1.2;
  }
  .contacts { position: absolute; right: 36px; top: 12px; display: flex; gap: 14px; }
  .contact { font-size: 10px; color: var(--white); line-height: 1.35; }
  .contact-name { font-weight: 700; font-size: 12.5px; color: var(--gold); }
  .contact-divider { width: 1px; background: var(--gold); opacity: .8; }
  .phone-icon { width: 9px; height: 9px; vertical-align: -1px; margin-right: 3px; fill: var(--gold); }
  .letter { position: absolute; left: 92px; top: 300px; width: 510px; }
  .salutation {
    font-family: "Montserrat", Arial, sans-serif; font-weight: 700; font-size: 15px;
    color: var(--ink); margin-bottom: 14px;
  }
  .letter p { font-size: 10.5px; line-height: 1.32; margin-bottom: 18px; }
  .closing { font-family: "Montserrat", Arial, sans-serif; font-weight: 600; font-size: 9px; margin-top: 6px; }
  .signature {
    display: block; width: 110px; height: 34px; margin-top: 14px; border-radius: 17px;
    background: linear-gradient(90deg, rgba(58,58,58,.18), rgba(58,58,58,.05));
  }
  .footer { position: absolute; left: 92px; right: 40px; bottom: 46px; display: flex; align-items: center; gap: 8px; }
  .footer-rule { flex: 1; height: 1px; background: var(--rule); }
  .footer-rule.short { flex: 0 0 40px; }
  .footer-address { font-size: 11px; color: var(--ink); white-space: nowrap; }
</style>
</head>
<body>
  <main class="letterhead">
    <svg class="header-wave" viewBox="0 0 680 200" aria-hidden="true">
      <path d="M0 0 H680 V52 C560 92 380 100 220 118 C120 130 50 140 0 158 Z" fill="var(--navy)"/>
      <path d="M0 170 C80 144 200 130 330 112 C200 136 90 152 0 178 Z" fill="var(--navy)"/>
      <path d="M0 184 C90 158 200 142 290 130 C190 152 90 170 0 196 Z" fill="var(--gold)"/>
    </svg>

    <div class="brand">
      <span class="brand-dot"></span>
      <span class="brand-name">Bluecrest Learning Corps</span>
    </div>

    <div class="contacts">
      <div class="contact">
        <div class="contact-name">Dr. Venrel T Oskamp</div>
        <div>CEO</div>
        <div><svg class="phone-icon" viewBox="0 0 10 10"><path d="M2 0h2l1 3-1.5 1c.5 1.2 1.3 2 2.5 2.5L7 5l3 1v2c0 1-1 2-2 2C4 10 0 6 0 2c0-1 1-2 2-2z"/></svg>(703) 482-1736</div>
      </div>
      <span class="contact-divider"></span>
      <div class="contact">
        <div class="contact-name">Marisa Deltoft</div>
        <div>Respresentative</div>
        <div><svg class="phone-icon" viewBox="0 0 10 10"><path d="M2 0h2l1 3-1.5 1c.5 1.2 1.3 2 2.5 2.5L7 5l3 1v2c0 1-1 2-2 2C4 10 0 6 0 2c0-1 1-2 2-2z"/></svg>(301) 647-2208</div>
      </div>
    </div>

    <section class="letter">
      <h1 class="salutation">Dear Mr. Halvern,</h1>
      <p>Lorem ipsum dolor sit amet, consectetuer adipiscing elit, sed diam nonmmy nibh euismod tincidunt ut laor eet dolore magna aliquam erat volutpat. Ut wisi enim ad minim veniam, quis nostrud exerci tationmcorper suscipit lobortis nisl ut aliquip ex ea commodo consequat. Duis autem vel eum iriure dolor in hendrerit in vulputate velit esse molestie consequat, vel illum dolore eu feugiat</p>
      <p>Rorem ipsum dolor sit amet, consectetuer adipiscing elit, sed diam nonmmy nibh euismod tincidunt ut laor eet dolore magna aliquam erat volutpat. Ut wisi enim ad minim veniam, quis nostrud exerci tationmcorper suscipit lobortis nisl ut aliquip ex ea commodo consequat. Duis autem vel eum iriure dolor in hendrerit in vulputate velit esse molest</p>
      <p>Dorem ipsum dolor sit amet, consectetuer adipiscing elit, sed diam nonmmy nibh euismod tincidunt ut laor eet dolore magna aliquam erat volutpat. Ut wisi enim ad minim veniam, quis nostrud exerci tationmcorper suscipit lobortis nisl ut aliquip ex ea commodo consequat. Duis autem vel eum iriure dolor in hendrerit in suscipit lobortis nisl ut aliquip ex ea commodo consequat. Duis autem vel eum iriure dolor in hendrerit in vulputate velit esse molestie consequat, vel illum</p>
      <p>Sorem ipsum dolor sit amet, consectetuer adipiscing elit, sed diam nonmmy nibh euismod tincidunt ut laor eet dolore magna aliquam erat volutpat. Ut wisi enim ad minim veniam, quis nostrud exerci tationmcorper suscipit lobortis nisl ut aliquip ex ea commodo consequat. Duis autem vel eum iriure dolor in</p>
      <div class="closing">Sincerely,</div>
      <span class="signature" role="img" aria-label="Handwritten signature"></span>
    </section>

    <footer class="footer">
      <span class="footer-rule"></span>
      <span class="footer-address">4719 Pellham Court, Ashbrook Station, VA 22184</span>
      <span class="footer-rule short"></span>
    </footer>
  </main>
</body>
</html>
```